Manufacturer's Representative Group needs a clean new Website

We represent and sell a number of suppliers that design and build products used in Biopharmaceutical manufacturing. Our sales region is in the central US. Our customer base is scientific / engineering based - so clean, we organized design with a focus on the products - easy and clear navigation is necessary. We do not sell direct or warehouse product - so e-commerce is not needed. Our customers will use the website for reference on what we do and offer - we will use the site as a platform to present products from each vendor and the home page will be used to capture an overview and draw users deeper into the site. You can view our current site - which needs A LOT of help to get ideas on products represented and types of products

Target Market(s)

Engineers and Pharmaceutical / Bio pharm end users

Industry/Entity Type

E-Commerce

Number of Pages Required

2 page

Font styles to use
Sans Serif

Requirements
Must have
• I need a home page that provides a snapshot of my company and the product lines we represent - then a second page that I can copy as a template for each line I rep as well as for an "About us / contact" page.
• I would like to be able to manage content on the pages so something easy to adjust pictures or add content is a must
• Must use our logo

```html
<!DOCTYPE html>
<html lang="en">
<head>
<meta charset="utf-8">
<title>Prairie Biosolutions</title>
<link href="https://fonts.googleapis.com/css2?family=Roboto:ital,wght@0,300;0,400;0,500;1,300;1,400&display=swap" rel="stylesheet">
<style>
:root{
  --orange:#e8630a;
  --navy:#0c1a6b;
  --footer:#0d1f80;
  --text:#555;
  --dark:#222;
  --band:#f3f3f3;
  --line:#dcdcdc;
  --white:#fff;
}
*{box-sizing:border-box;margin:0;padding:0}
html,body{width:847px;height:1200px;overflow:hidden;background:var(--white);font-family:'Roboto',sans-serif;color:var(--text)}
.page{position:relative;width:847px;height:1200px}
.abs{position:absolute}
.search{left:649px;top:5px;width:146px;height:22px;border:1px solid var(--line);border-radius:2px;font:italic 300 8px 'Roboto',sans-serif;color:#999;padding:6px 9px}
.search svg{position:absolute;right:6px;top:5px}
.topline{left:52px;top:32px;width:743px;height:1px;background:var(--line)}
.brand{left:52px;top:44px;display:flex;align-items:center;gap:7px;font:400 21px 'Roboto',sans-serif;color:var(--navy)}
.brand i{width:12px;height:12px;border-radius:50%;background:var(--orange);display:block}
.nav{top:55px;font:400 8.5px 'Roboto',sans-serif;color:#333;letter-spacing:.2px}
.nav.active{color:var(--navy);font-weight:500}
.hero{left:52px;top:81px;width:743px;height:296px;border:3px solid #e4e4e4}
.hero-bg{width:100%;height:100%;background:linear-gradient(180deg,#d6e6f3 0%,#8ebde2 55%,#3d8fd0 100%);position:relative}
.hero-media{position:absolute;right:0;top:0;width:440px;height:100%;background:radial-gradient(ellipse at 60% 55%,#e3e6ea 0%,#b9c3cc 35%,rgba(160,190,215,0) 70%)}
.hero h1{position:absolute;left:26px;top:66px;font:400 32px 'Roboto',sans-serif;color:var(--orange);letter-spacing:.3px}
.hero p{position:absolute;left:28px;top:105px;width:325px;font:400 10.3px/15px 'Roboto',sans-serif;color:#222}
.btn{background:var(--navy);color:var(--white);font:500 9px 'Roboto',sans-serif;display:flex;align-items:center;justify-content:center;border-radius:2px}
.hero .btn{position:absolute;left:25px;top:174px;width:103px;height:28px}
.dots{position:absolute;left:26px;top:267px;display:flex;gap:5px}
.dots span{width:7px;height:7px;border-radius:50%;background:var(--white)}
.dots span:first-child{background:var(--orange)}
.section-title{font:400 16px 'Roboto',sans-serif;color:var(--orange);letter-spacing:.3px}
.center{left:0;width:847px;text-align:center}
.about-text{left:52px;top:434px;width:743px;text-align:center;font:300 9.2px/15.2px 'Roboto',sans-serif;color:#444;letter-spacing:.05px}
.band{left:0;width:847px;background:var(--band)}
.arrow{width:22px;height:22px;border-radius:50%;background:var(--white);border:1px solid var(--line);display:flex;align-items:center;justify-content:center}
.card{top:577px;width:171px;height:179px;background:#f1f1f1;border:1px solid #e2e2e2}
.card .img{height:126px}
.card h3{position:absolute;left:10px;top:139px;font:400 11.5px 'Roboto',sans-serif;color:var(--orange)}
.card small{position:absolute;left:10px;top:158px;font:italic 300 8px 'Roboto',sans-serif;color:#555}
.card .btn{position:absolute;left:121px;top:142px;width:37px;height:23px;font-size:8.5px}
.col-title{top:809px;font:400 15px 'Roboto',sans-serif;color:var(--orange);letter-spacing:.3px}
.thumb{top:842px;width:126px;height:95px}
.post h4{font:400 15.5px 'Roboto',sans-serif;color:var(--dark);letter-spacing:.2px}
.post .from{margin-top:6px;font:italic 400 9px 'Roboto',sans-serif;color:var(--orange);display:flex;align-items:center;gap:6px}
.post .from b{font:normal 400 9px 'Roboto',sans-serif;color:#333}
.post p{margin-top:8px;width:208px;font:300 9px/13px 'Roboto',sans-serif;color:#333}
.partners{left:52px;top:1040px;width:743px;display:flex;justify-content:space-between;align-items:center}
.partner{display:flex;align-items:center;gap:5px;font:400 12px 'Roboto',sans-serif;color:#2a4a7a;height:40px}
.partner i{width:10px;height:10px;border-radius:50%;background:#2a8a9a;display:block}
.footer{left:0;top:1118px;width:847px;height:82px;background:var(--footer);color:#d8dcf0}
.footer .copy{position:absolute;left:52px;top:29px;font:400 7.5px/14px 'Roboto',sans-serif}
.footer .connect{position:absolute;left:661px;top:36px;font:400 8px 'Roboto',sans-serif;color:var(--white)}
.social{position:absolute;top:29px;width:21px;height:21px;border-radius:50%}
</style>
</head>
<body>
<div class="page">
  <header>
    <div class="abs search">Search..
      <svg width="11" height="11" viewBox="0 0 11 11"><circle cx="4" cy="4" r="3" fill="none" stroke="#e8630a" stroke-width="1.5"/><line x1="6.2" y1="6.2" x2="10" y2="10" stroke="#e8630a" stroke-width="2"/></svg>
    </div>
    <div class="abs topline"></div>
    <div class="abs brand"><i></i>Prairie Bio</div>
    <nav>
      <span class="abs nav active" style="left:526px">HOME</span>
      <span class="abs nav" style="left:586px">ABOUT US</span>
      <span class="abs nav" style="left:662px">PRODUCTS</span>
      <span class="abs nav" style="left:742px">CONTACT US</span>
    </nav>
  </header>

  <section class="abs hero">
    <div class="hero-bg">
      <div class="hero-media" role="img" aria-label="Stainless steel vial filling machine with peristaltic pump"></div>
      <h1>PRAIRIE BIOSOLUTIONS</h1>
      <p>Prairie Biosolutions is a distribution channel, licensed partner and manufacturers representative group providing high quality fluid handling products and technical services to the Midwestern biopharmaceutical community.</p>
      <div class="btn">VIEW ALL PRODUCTS</div>
      <div class="dots"><span></span><span></span><span></span><span></span></div>
    </div>
  </section>

  <section>
    <h2 class="abs center section-title" style="top:406px">ABOUT US</h2>
    <p class="abs about-text">Prairie Biosolutions is a distribution channel, licensed partner and manufacturers representative group providing high quality fluid handling products and technical services to the Midwestern biopharmaceutical community. With a core staff of experienced professionals and a team approach to all customer needs, we offer over 30 years of cGMP experience in the selection and use of most process consumable products. We're looking forward to working with you!</p>
  </section>

  <section class="abs band" style="top:510px;height:273px"></section>
  <div class="abs arrow" style="left:52px;top:535px"><svg width="8" height="8" viewBox="0 0 8 8"><path d="M5 1L2 4l3 3" fill="none" stroke="#333" stroke-width="1.2"/></svg></div>
  <div class="abs arrow" style="left:773px;top:535px"><svg width="8" height="8" viewBox="0 0 8 8"><path d="M3 1l3 3-3 3" fill="none" stroke="#333" stroke-width="1.2"/></svg></div>
  <h2 class="abs center section-title" style="top:536px">FEATURED PRODUCTS</h2>

  <article class="abs card" style="left:52px">
    <div class="img" role="img" aria-label="Single-use bioprocess bag with tubing" style="background:linear-gradient(135deg,#f2f6f8,#b9dcef)"></div>
    <h3>Product Name</h3><small>Mauris et massa sed&nbsp; amet</small><div class="btn">Info</div>
  </article>
  <article class="abs card" style="left:242px">
    <div class="img" role="img" aria-label="Blue peristaltic pump" style="background:linear-gradient(135deg,#3a62b5,#8a8f96 60%,#d9d0bd)"></div>
    <h3>Product Name</h3><small>Mauris et massa sed&nbsp; amet</small><div class="btn">Info</div>
  </article>
  <article class="abs card" style="left:433px">
    <div class="img" role="img" aria-label="Assorted silicone fittings and caps" style="background:radial-gradient(circle at 55% 45%,#c9d6ea,#3a5390 55%,#0f1d45)"></div>
    <h3>Product Name</h3><small>Mauris et massa sed&nbsp; amet</small><div class="btn">Info</div>
  </article>
  <article class="abs card" style="left:624px">
    <div class="img" role="img" aria-label="Red benchtop peristaltic pump" style="background:linear-gradient(135deg,#d9353a,#9b1c22 60%,#d8c8a8)"></div>
    <h3>Product Name</h3><small>Mauris et massa sed&nbsp; amet</small><div class="btn">Info</div>
  </article>

  <section>
    <h2 class="abs col-title" style="left:52px">UPDATES</h2>
    <div class="abs thumb" style="left:52px;background:linear-gradient(180deg,#eef0f3,#b8c2cc)" role="img" aria-label="Clear plastic pharmaceutical bottles"></div>
    <div class="abs post" style="left:192px;top:840px;width:225px">
      <h4>Certified Clean Pureflasks</h4>
      <div class="from">From <b>PureVessel</b></div>
      <p>Meeting USP 788 Particulate Matter in Injections, and the equivalent EP and JP quality standards. We offer these in standard and custom configurations!</p>
    </div>

    <h2 class="abs col-title" style="left:443px">PB CALIBRA SOLUTIONS</h2>
    <div class="abs thumb" style="left:444px;background:linear-gradient(90deg,#a9d84a,#d8dadc 55%,#a8adb2)" role="img" aria-label="Bioreactor system on a wheeled cart"></div>
    <div class="abs post" style="left:583px;top:840px;width:215px">
      <h4>Certified Clean Pureflasks</h4>
      <div class="from">From <b>Calibra</b></div>
      <p>We are proud to announce that we now represent the Calibra Solutions array of Reactors, Controllers, Sensors and Service</p>
    </div>
  </section>

  <section class="abs band" style="top:972px;height:146px"></section>
  <h2 class="abs center section-title" style="top:998px">COMPANIES REPRESENTED</h2>
  <div class="abs partners">
    <div class="partner"><i></i>PureVessel</div>
    <div class="partner">Calibra</div>
    <div class="partner">Flexline Hose Co</div>
    <div class="partner">ModuCell Systems</div>
    <div class="partner">Norvane Polymers</div>
    <div class="partner">Harlow Pump Group</div>
  </div>

  <footer class="abs footer">
    <div class="copy">COPYRIGHT © 2014 PRAIRIE BIOSOLUTIONS, CORP.<br>ALL RIGHT RESERVED</div>
    <div class="connect">CONNECT US:</div>
    <span class="social" style="left:722px;background:#3b5998" aria-label="Social link"></span>
    <span class="social" style="left:748px;background:#2aa3e0" aria-label="Social link"></span>
    <span class="social" style="left:774px;background:#f58a1f" aria-label="News feed"></span>
  </footer>
</div>
</body>
</html>
```